Lurvik.no is a new website about pedagogical entrepreneurship. It's main target group is teachers. The Nordic Bureau for Digital Schooling and the National Office for Learning and Classrooms are leading the project.

The web page is meant to show examples of how different methods of entrepreneurship can be used pedagogical in a learning environment. The page will also support the user with examples of different teaching programs and other examples of best practice.

Pedagogical entrepreneurship is not about business and men in suits. It's a method for learning. The focus in the design should be on school, education and new ways of learning.

The final product should be motivating and engaging, but at the same time governmental and serious. We are not looking for something "flashy" and corporate-looking, but a moderate, task-focused and clean design that state quality.

We need designs for three pages:
1 - frontpage
2 - subpage ("Metoder og undervisningsopplegg")
3 - subpage ("Små-TOPP i Vassbygd")

The interaction design for these three pages will be uploaded as an attachment.

We would like you to find inspiration in the following websites:
- www.skapekraft.no
- www.giellu.no
- www.brightfernlab.com
- www.zyx.no
(more will be added)

Please use the attached logo, and feel free to use this as an inspiration for the rest of the design.

Target Market(s)

Teachers

Industry/Entity Type

Education

Requirements
Must have
• * Header with: Logo. Main navigation. Utility navigation. Search box.
* Footer
Should not have
• Images of men in suits.
Very strong graphical elements that stands out too much (we want it clean).

```html
<!DOCTYPE html>
<html lang="en">
<head>
<meta charset="utf-8">
<title>Lurvik.no – Pedagogical entrepreneurship</title>
<link rel="stylesheet" href="https://fonts.googleapis.com/css2?family=Noto+Serif:ital,wght@1,400;1,700&family=Oswald:wght@300;400&family=PT+Sans:wght@400;700&display=swap">
<style>
  :root {
    --brand: #1a72bd;
    --brand-light: #3fa3e0;
    --pill: #45a6e2;
    --pill-dark: #1f7cc4;
    --navy: #1c3566;
    --banner: #1d4a7e;
    --sky-top: #2a8fd6;
    --sky-mid: #3aa4e6;
    --floor: #1c4f8c;
    --panel-bg: #dde6ee;
    --text: #333333;
    --muted: #666666;
    --link: #1a7fc0;
    --yellow: #f5c400;
    --white: #ffffff;
    --sans: "PT Sans", Arial, sans-serif;
    --serif: "Noto Serif", Georgia, serif;
    --cond: "Oswald", "Arial Narrow", sans-serif;
  }
  * { box-sizing: border-box; margin: 0; padding: 0; }
  html, body { width: 883px; height: 1200px; overflow: hidden; background: var(--white); }
  body { position: relative; font-family: var(--sans); color: var(--text); }
  a { color: inherit; text-decoration: none; }
  ul { list-style: none; }

  /* Header */
  .site-header { position: absolute; left: 0; top: 0; width: 883px; height: 82px; background: var(--white); }
  .brand { position: absolute; left: 103px; top: 14px; display: flex; align-items: center; gap: 12px; }
  .brand-mark { width: 48px; height: 48px; background: var(--brand); border-radius: 50%; }
  .brand-name { font-family: var(--sans); font-weight: 700; font-size: 40px; line-height: 1; color: var(--brand); }
  .brand-tagline { position: absolute; left: 174px; top: 57px; font-size: 9px; color: var(--brand); }
  .search { position: absolute; left: 605px; top: 16px; width: 173px; height: 16px; display: flex; }
  .search input { width: 158px; height: 16px; border: 1px solid #c8c8c8; font: 9px var(--sans); padding: 0 4px; color: #555; }
  .search button { width: 15px; height: 16px; border: 0; background: var(--navy); display: grid; place-items: center; }
  .main-nav { position: absolute; top: 46px; left: 428px; display: flex; gap: 4px; }
  .main-nav a { display: block; height: 20px; line-height: 20px; padding: 0 9px; border-radius: 10px; background: linear-gradient(#5cb7ee, var(--pill-dark)); color: var(--white); font-size: 10.5px; letter-spacing: .2px; box-shadow: inset 0 0 0 1px rgba(255,255,255,.35); }

  /* Hero */
  .hero { position: absolute; left: 0; top: 82px; width: 883px; height: 421px; background: linear-gradient(180deg, var(--sky-top) 0%, var(--sky-mid) 45%, #2a86cf 90%); overflow: hidden; }
  .hero-floor { position: absolute; left: 0; bottom: 0; width: 100%; height: 48px; background: var(--floor); }
  .hero-banner { position: absolute; left: 103px; top: -6px; width: 675px; height: 91px; background: var(--banner); border-radius: 0 0 3px 3px; padding: 9px 20px; font-family: var(--serif); font-style: italic; font-size: 15.5px; line-height: 20px; color: var(--white); }
  .hero-banner strong { font-weight: 700; }
  .hero-banner .more { position: absolute; right: 16px; bottom: 16px; font-size: 15px; color: #8fd0ff; }
  .pillar { position: absolute; top: 114px; width: 230px; text-align: center; color: var(--white); }
  .pillar .kicker { font-size: 13.5px; }
  .pillar .title { font-family: var(--cond); font-weight: 300; font-size: 24px; line-height: 25px; margin-top: 6px; }
  .pillar-art { position: absolute; top: 210px; width: 215px; height: 210px; border-radius: 3px; }

  /* Middle */
  .tools { position: absolute; left: 0; top: 503px; width: 883px; height: 284px; background: var(--panel-bg); }
  .meter-box { position: absolute; left: 103px; top: 14px; width: 205px; height: 238px; background: linear-gradient(#f2f6fa, #dfe8f0); border-radius: 4px; box-shadow: 0 1px 3px rgba(0,0,0,.2); }
  .meter-box h2 { height: 51px; background: linear-gradient(#1d80cc, #1664a8); border-radius: 4px 4px 0 0; color: var(--white); font-weight: 400; font-size: 17px; line-height: 17px; padding: 8px 14px; }
  .meter-art { position: absolute; left: 29px; top: 62px; width: 152px; height: 152px; border-radius: 50%; background: radial-gradient(circle, #2b2f33 55%, #a9b2b9 60%, #e8ecef 70%); }
  .meter-cta { position: absolute; left: 15px; top: 219px; width: 176px; height: 35px; background: linear-gradient(#ffd92e, var(--yellow)); border-radius: 4px; color: var(--navy); font-weight: 700; font-size: 16px; line-height: 35px; text-align: center; box-shadow: 0 1px 2px rgba(0,0,0,.3); }
  .start-panel { position: absolute; left: 322px; top: 14px; width: 455px; height: 258px; background: linear-gradient(#ffffff, #e4ecf3); border-radius: 4px; box-shadow: 0 1px 3px rgba(0,0,0,.2); }
  .start-panel h2 { position: absolute; left: 15px; top: 14px; width: 425px; height: 25px; border-radius: 13px; background: linear-gradient(#ffffff, #d8dcdf); border: 1px solid #b9bec2; font-size: 16px; font-weight: 700; color: #333; padding-left: 11px; line-height: 23px; }
  .list-col { position: absolute; top: 55px; width: 175px; }
  .list-col h3 { font-size: 10px; font-weight: 700; color: var(--link); padding-bottom: 8px; border-bottom: 1px dotted #aab; margin-bottom: 9px; }
  .list-col li { font-size: 8.5px; line-height: 17px; padding-left: 15px; position: relative; }
  .list-col li::before { content: ""; position: absolute; left: 0; top: 4px; width: 9px; height: 9px; border-radius: 50%; background: var(--brand-light); }
  .see-more { position: absolute; top: 229px; font-size: 8.5px; color: var(--link); }

  /* Inspiration */
  .inspiration h2 { position: absolute; left: 125px; top: 806px; font-size: 21px; font-weight: 400; color: var(--link); }
  .card { position: absolute; top: 854px; width: 142px; }
  .card h3 { font-size: 12px; font-weight: 400; line-height: 14px; color: #333; height: 41px; }
  .card-photo { width: 142px; height: 95px; }
  .arrow { position: absolute; top: 938px; }

  /* Footer */
  .site-footer { position: absolute; left: 0; top: 1018px; width: 883px; height: 182px; background: var(--navy); color: var(--white); }
  .footer-brand { position: absolute; left: 103px; top: 56px; font-size: 30px; font-weight: 700; color: #8fc4ee; }
  .footer-col { position: absolute; top: 20px; }
  .footer-col h3 { font-size: 10.5px; font-weight: 700; margin-bottom: 7px; }
  .footer-col li { font-size: 8.5px; line-height: 16px; color: #dfe7f2; }
  .footer-col li.more { color: var(--yellow); }
  .copyright { position: absolute; left: 104px; top: 154px; font-size: 9px; }
  .share { position: absolute; left: 675px; top: 152px; display: flex; align-items: center; gap: 4px; font-size: 11px; }
  .share span.box { width: 16px; height: 16px; background: #5a86c8; display: inline-block; }
  .share span.box + span.box { background: #4aa9de; }
</style>
</head>
<body>

<header class="site-header">
  <a class="brand" href="#"><span class="brand-mark"></span><span class="brand-name">Lurvik</span></a>
  <p class="brand-tagline">Entreprenørielle metoder i undervisningen</p>
  <form class="search" role="search">
    <input type="text" placeholder="Search" aria-label="Search">
    <button type="submit" aria-label="Search">
      <svg width="9" height="9" viewBox="0 0 9 9"><circle cx="3.6" cy="3.6" r="2.6" fill="none" stroke="#fff" stroke-width="1.3"/><line x1="5.5" y1="5.5" x2="8.3" y2="8.3" stroke="#fff" stroke-width="1.5"/></svg>
    </button>
  </form>
  <nav class="main-nav">
    <a href="#">BEST PRACTICE SCHOOLS</a>
    <a href="#">LURVIKMETER</a>
    <a href="#">ABOUT LURVIK.NO</a>
  </nav>
</header>

<section class="hero">
  <div class="hero-floor"></div>
  <div class="hero-banner">
    <strong>Pedagogical entrepreneurship works.</strong> Lorem ipsum dolor sit amet, consectetur adipisicing elit, sed do eiusmod tempor incididunt ut labore et dolore magna aliqua.
    <a class="more" href="#">Learn more ›</a>
  </div>

  <div class="pillar" style="left:93px"><p class="kicker">Learn about what, why and how!</p><p class="title">What is pedagocical<br>entrepreneurship?</p></div>
  <div class="pillar" style="left:325px"><p class="kicker">Plan your lessons!</p><p class="title">Methods and<br>teaching plans</p></div>
  <div class="pillar" style="left:561px;top:118px"><p class="kicker">Be inspired!</p><p class="title">Good examples /<br>best practice</p></div>

  <div class="pillar-art" role="img" aria-label="Illustration: character pointing at a screen with a solution list" style="left:98px;background:linear-gradient(#f4f6f8 0%, #e9eef2 60%, #5db3ea 61%, #5db3ea 100%)"></div>
  <div class="pillar-art" role="img" aria-label="Illustration: character pointing at a screen showing think, idea, try, do, success" style="left:333px;background:linear-gradient(#f4f6f8 0%, #e9eef2 60%, #5db3ea 61%, #5db3ea 100%)"></div>
  <div class="pillar-art" role="img" aria-label="Illustration: character pointing at a screen with a checklist" style="left:570px;background:linear-gradient(#f4f6f8 0%, #e9eef2 60%, #5db3ea 61%, #5db3ea 100%)"></div>
</section>

<section class="tools">
  <div class="meter-box">
    <h2>Are you working<br>entrepreneurship-like?</h2>
    <div class="meter-art" role="img" aria-label="Illustration: speedometer gauge"></div>
    <a class="meter-cta" href="#">Try the lurvikmeter!</a>
  </div>

  <div class="start-panel">
    <h2>Get started!</h2>
    <div class="list-col" style="left:19px">
      <h3>Methods</h3>
      <ul><li>Cafe-pedagogikk</li><li>Elevbedrift</li><li>Grundercamp</li><li>Story line</li><li>REAL</li><li>Grundercamp</li><li>Story line</li><li>REAL</li></ul>
    </div>
    <a class="see-more" href="#" style="left:19px">See more…</a>
    <div class="list-col" style="left:238px">
      <h3>Teaching plans</h3>
      <ul><li>Teaching plans title</li><li>Teaching plans title</li><li>Teaching plans title</li><li>Teaching plans title</li><li>Teaching plans title</li><li>Teaching plans title</li><li>Teaching plans title</li><li>Teaching plans title</li></ul>
    </div>
    <a class="see-more" href="#" style="left:238px">See more…</a>
  </div>
</section>

<section class="inspiration">
  <h2>Inspiration</h2>
  <svg class="arrow" style="left:109px" width="8" height="10" viewBox="0 0 8 10"><path d="M7 0 L0 5 L7 10Z" fill="#888"/></svg>
  <svg class="arrow" style="left:765px" width="8" height="10" viewBox="0 0 8 10"><path d="M1 0 L8 5 L1 10Z" fill="#888"/></svg>
  <article class="card" style="left:125px"><h3>Lorem ipsum dolor<br>sed do eiusmod</h3><div class="card-photo" role="img" aria-label="Photo: students working together around a table" style="background:linear-gradient(135deg,#b5523a,#d9b89a 50%,#6c7a8a)"></div></article>
  <article class="card" style="left:289px;top:858px"><h3>Lorem ipsum dolor<br>sed do eiusmod</h3><div class="card-photo" role="img" aria-label="Photo: group attending a workshop" style="background:linear-gradient(135deg,#9aa7b3,#e3e0da 50%,#7a8491)"></div></article>
  <article class="card" style="left:452px;top:858px"><h3>Lorem ipsum dolor<br>sed do eiusmod</h3><div class="card-photo" role="img" aria-label="Photo: teacher in a classroom" style="background:linear-gradient(135deg,#d2a36a,#2f7fc4 55%,#c94a3a)"></div></article>
  <article class="card" style="left:616px;top:858px"><h3>Lorem ipsum dolor<br>sed do eiusmod</h3><div class="card-photo" role="img" aria-label="Photo: cheerful group of people" style="background:linear-gradient(135deg,#e9eef3,#8d9aa8 55%,#3a3f47)"></div></article>
</section>

<footer class="site-footer">
  <p class="footer-brand">Lurvik</p>
  <div class="footer-col" style="left:231px"><h3>Pedagogical entrepreneurship</h3><ul><li>What is pedagogical entrepreneurship?</li><li>Science</li><li>Best practice schools</li><li>Lurvikmeter</li><li>About lurvik.no</li></ul></div>
  <div class="footer-col" style="left:432px"><h3>Methoda</h3><ul><li>Storyline</li><li>REAL</li><li>Cafe-pedagogikk</li><li class="more">See more…</li></ul></div>
  <div class="footer-col" style="left:549px"><h3>Teaching plans</h3><ul><li>Lorem ipsum dolor</li><li>sed do eiusmod</li><li>Lorem ipsum dolor</li><li>sed do eiusmod</li><li class="more">See more…</li></ul></div>
  <div class="footer-col" style="left:677px"><h3>Gode eksemplert</h3><ul><li>Lorem ipsum dolor</li><li>sed do eiusmod</li><li>Lorem ipsum dolor</li><li>sed do eiusmod</li><li class="more">See more…</li></ul></div>
  <p class="copyright">© 2011 Pedagogical entrepreneurship.</p>
  <div class="share">Share this! <span class="box"></span><span class="box"></span></div>
</footer>

</body>
</html>
```